Award-winnning Estate Agent needs a premium version of their 'For Sale' board design

We need a premium option for our 'For Sale' board design. We have a standard board that is attached to this brief, but were are looking to have a premium design version that we will use when selling exclusive properties. Our company name is Harbourline Vale Estates and the name for this is exclusive selection is: 'The Harbourline Collection'. The design needs to work with our current brand, but have a distinctive PREMIUM feel to it. I have uploaded the barnd guidelines and also some of the exisisting logo variations. We do NOT need a new logo but feel free to play around with colours, fonts, sizes etc. for the sign.

Target Market(s)

Property buyers & house hunters

Industry/Entity Type

Real Estate - Residential Property

Font styles to use
Sans Serif

Requirements
Must have
• A premium fee, must be square design, must be easy to read when driving past the sign
Nice to have
• I'm open ot ideas

```html
<!DOCTYPE html>
<html lang="en">
<head>
<meta charset="utf-8">
<title>Harbourline Vale Estates – The Harbourline Collection For Sale Board</title>
<link rel="stylesheet" href="https://fonts.googleapis.com/css2?family=Arimo:wght@400;700&display=swap">
<style>
  :root {
    --page-bg: #e6e6e6;
    --navy: #2e2a80;
    --sky: #33a5ff;
    --sky-deep: #2b95ec;
    --brand-purple: #3d2a73;
    --white: #ffffff;
    --ink: #000000;
  }
  * { box-sizing: border-box; margin: 0; padding: 0; }
  html, body {
    width: 715px;
    height: 1200px;
    overflow: hidden;
    background: var(--page-bg);
    font-family: "Arimo", Arial, sans-serif;
  }
  .board {
    position: absolute;
    left: 57px;
    top: 300px;
    width: 600px;
    height: 600px;
    background: var(--white);
    box-shadow: 0 6px 10px rgba(0,0,0,0.35);
    overflow: hidden;
  }
  .board__frame {
    position: absolute;
    inset: 8px 8px 8px 8px;
    border: 1px solid var(--navy);
    pointer-events: none;
    z-index: 2;
  }
  .board__corner {
    position: absolute;
    top: 0;
    width: 161px;
    height: 117px;
    background: var(--navy);
  }
  .board__corner--left { left: 0; clip-path: polygon(0 0, 100% 0, 0 100%); }
  .board__corner--right { right: 0; clip-path: polygon(0 0, 100% 0, 100% 100%); }

  .collection {
    position: absolute;
    left: 0;
    right: 0;
    top: 86px;
    text-align: center;
  }
  .collection__label {
    display: inline-block;
    font-size: 17px;
    font-weight: 700;
    letter-spacing: 4px;
    text-transform: uppercase;
    color: var(--navy);
    padding: 0 0 8px;
    border-bottom: 2px solid var(--sky);
  }

  .brand {
    position: absolute;
    left: 0;
    right: 0;
    top: 160px;
    display: flex;
    justify-content: center;
    align-items: center;
    gap: 12px;
  }
  .brand__mark {
    width: 22px;
    height: 22px;
    background: var(--sky-deep);
  }
  .brand__name {
    font-size: 36px;
    font-weight: 700;
    color: var(--brand-purple);
    letter-spacing: -0.5px;
    line-height: 1;
  }

  .rule { position: absolute; left: 0; right: 0; background: var(--navy); }
  .rule--upper { top: 223px; height: 16px; }
  .rule--lower { top: 382px; height: 16px; }
  .rule--base { top: 587px; height: 13px; }

  .sale-band {
    position: absolute;
    left: 0;
    right: 0;
    top: 239px;
    height: 143px;
    background: var(--sky);
  }
  .sale-band__skyline {
    position: absolute;
    left: 12px;
    right: 16px;
    bottom: 0;
    height: 90px;
    background: linear-gradient(to top, rgba(120,195,255,0.55), rgba(51,165,255,0));
  }
  .sale-band__title {
    position: absolute;
    left: 0;
    right: 0;
    top: 18px;
    text-align: center;
    font-size: 110px;
    font-weight: 700;
    line-height: 1;
    color: var(--white);
    letter-spacing: -3px;
  }

  .contact {
    position: absolute;
    left: 0;
    right: 0;
    top: 398px;
    height: 127px;
    display: flex;
    align-items: center;
    padding-left: 32px;
    gap: 12px;
  }
  .contact__icon { width: 82px; height: 82px; flex: none; }
  .contact__number {
    font-size: 68px;
    font-weight: 700;
    color: var(--ink);
    letter-spacing: -1.5px;
    line-height: 1;
  }

  .web-band {
    position: absolute;
    left: 0;
    right: 0;
    top: 525px;
    height: 62px;
    background: var(--sky);
    display: flex;
    justify-content: center;
    align-items: center;
  }
  .web-band__url {
    font-size: 32px;
    font-weight: 700;
    color: var(--white);
    letter-spacing: -1px;
  }
</style>
</head>
<body>
  <div class="board">
    <div class="board__corner board__corner--left"></div>
    <div class="board__corner board__corner--right"></div>

    <div class="collection">
      <span class="collection__label">The Harbourline Collection</span>
    </div>

    <div class="brand">
      <span class="brand__mark"></span>
      <span class="brand__name">Harbourline Vale Estates</span>
    </div>

    <div class="rule rule--upper"></div>
    <div class="sale-band">
      <div class="sale-band__skyline" role="img" aria-label="Faint line drawing of a city skyline with towers and palm trees"></div>
      <div class="sale-band__title">FOR SALE</div>
    </div>
    <div class="rule rule--lower"></div>

    <div class="contact">
      <svg class="contact__icon" viewBox="0 0 82 82" aria-hidden="true">
        <circle cx="41" cy="41" r="39" fill="var(--sky)"/>
        <circle cx="41" cy="41" r="34" fill="var(--navy)"/>
        <path d="M27 22c2-2 4-2 5 0l5 8c1 2 0 3-1 4l-3 3c2 5 6 9 11 11l3-3c1-1 2-2 4-1l8 5c2 1 2 3 0 5l-4 4c-3 3-9 2-16-3s-13-12-16-18c-2-6-2-10 0-12z" fill="var(--white)"/>
        <path d="M44 24a14 14 0 0 1 14 14" fill="none" stroke="var(--white)" stroke-width="3.5" stroke-linecap="round"/>
        <path d="M44 31a7 7 0 0 1 7 7" fill="none" stroke="var(--white)" stroke-width="3.5" stroke-linecap="round"/>
      </svg>
      <span class="contact__number">01632 960481</span>
    </div>

    <div class="web-band">
      <span class="web-band__url">www.harbourlinevaleestates.co.uk</span>
    </div>
    <div class="rule rule--base"></div>
  </div>
</body>
</html>
```